Verpackungen für Sekt/Champagner Flaschen
Zielgruppe
Dekoration für Hochzeiten. Tisch Dekoration für Hochzeiten. Zielgruppe alles was mit Hochzeiten zutun hat
Aufgabenstellung
Wir lassen gerade ein Tube/Dose herstellen, die als Umverpackung oder einfach Verpackung für Sekt/Champagne Flaschen dienen soll die dann auf die Tische für Hochzeit´s Deko kommt um die die Tisch Deko aufzubessern, statt einfach nur eine Sekt Flasche stehen zu haben. .Die Tube wird komplett in weiß sein und alles andere an Design soll in einem Gold sein. Mr&Mrs oder Just Married mit Herzen und alles was sonst dazu gehört, da lassen wir freie Hand.
Das Design soll Schlicht sein aber auch Luxuriös.
Durchmesser der Tube wird 8,5 cm haben und 34-35 cm sein.
Die Goldene Schrift und das Muster soll am Ende in einem Relief Lack auf der Tube erscheinen

```html
<!DOCTYPE html>
<html lang="de">
<head>
<meta charset="utf-8">
<title>Mr&amp;Mrs – Banderole</title>
<link rel="stylesheet" href="https://fonts.googleapis.com/css2?family=Oranienbaum&display=swap">
<style>
  :root {
    --paper: #ffffff;
    --gold-line: #c69c6d;
    --gold-type: #8d7049;
    --flourish-brown: #d8cfc8;
  }
  html, body {
    margin: 0;
    padding: 0;
    background: var(--paper);
    overflow: hidden;
  }
  .banderole {
    display: block;
    width: 1200px;
    height: 287px;
    background: var(--paper);
  }
  .rule { fill: var(--gold-line); }
  .title-frame {
    fill: none;
    stroke: var(--gold-line);
    stroke-width: 6;
  }
  .title-text {
    font-family: "Oranienbaum", "Times New Roman", serif;
    font-size: 122px;
    fill: var(--gold-type);
  }
  .flourish { fill: var(--flourish-brown); }
</style>
</head>
<body>
<svg class="banderole" viewBox="0 0 1200 287" xmlns="http://www.w3.org/2000/svg">
  <!-- left double rule -->
  <rect class="rule" x="0" y="144" width="441" height="8"/>
  <rect class="rule" x="0" y="159" width="441" height="8"/>
  <!-- right double rule -->
  <rect class="rule" x="759" y="144" width="441" height="8"/>
  <rect class="rule" x="759" y="159" width="441" height="8"/>

  <!-- flourish ornaments -->
  <rect class="flourish" x="138" y="99" width="178" height="34" rx="17" role="img" aria-label="Goldene Schnörkel-Ornamentik oben links"/>
  <rect class="flourish" x="138" y="182" width="178" height="38" rx="19" role="img" aria-label="Goldene Schnörkel-Ornamentik unten links"/>
  <rect class="flourish" x="876" y="99" width="178" height="34" rx="17" role="img" aria-label="Goldene Schnörkel-Ornamentik oben rechts"/>
  <rect class="flourish" x="876" y="182" width="178" height="38" rx="19" role="img" aria-label="Goldene Schnörkel-Ornamentik unten rechts"/>

  <!-- central title plate -->
  <rect class="title-frame" x="465" y="77" width="267" height="134"/>
  <text class="title-text" x="598" y="188" text-anchor="middle" textLength="222" lengthAdjust="spacingAndGlyphs">Mr&amp;Mrs</text>
</svg>
</body>
</html>
```